Business card for Crestline Bathrooms

Please design a business card for our bathroom renovation business. You can use my existing logo, but if you have an idea to modernize it, I would like to see it. Please see attached files first. I would like to use the blue and the orange theme. I like the concept of using the shower head in the logo. Please find following a design (or two) that I have been trying to create with my limited resources. That design was for a sign, but I was going to adopt it and use it as a business card as well. I like the concept of the water splash but I don’t think it “flows” nicely together with the logo. Another thought is that maybe creating the logo out of water splash could work and have a dramatic effect (like the water text and the butterfly picture attached with similar background instead of white). If the above doesn’t work I would like to see a modern simplified design. One of the attached files named as the unwanted business card has all the details that I want included in the business card. Please note that it is two sided.
Updates

I am very thankful for the designs that I have received, but they are very similar and only a couple of attempts to do something with the water splash as per my original brief. Modernizing the logo and having it made out of out of water splash with the orange as color accent could work and have a dramatic effect (like the water text and the butterfly picture attached with similar background instead of white). Please do not use the butterfly itself! This is just an example that images can be created out of water splash.

Contact Information for Business Card

all the details are on the unwonted business card file included

Colors
3176b5

Requirements
Nice to have
• Copied from the brief:
• ... maybe creating the logo out of water splash could work and have a dramatic effect (like the water text and the butterfly picture attached with similar background instead of white). Please do not use the butterfly itself!
Should not have
• I am getting designs with a butterfly. The butterfly picture was an example of creating something from a water splash. The butterfly itself has no association with anything other than the concept of creating a logo out of water splash. Sorry, I thought I was clear in the brief.

```html
<!DOCTYPE html>
<html lang="en">
<head>
<meta charset="utf-8">
<title>Crestline Bathrooms – Business Card</title>
<link rel="stylesheet" href="https://fonts.googleapis.com/css2?family=Roboto:wght@400;500;700&family=Patrick+Hand&display=swap">
<style>
  :root {
    --backdrop: #e4e4e4;
    --navy: #172d50;
    --navy-deep: #0f2140;
    --splash-light: #c9d6e3;
    --splash-mid: #5f7896;
    --coral: #ea7a68;
    --white: #ffffff;
  }
  * { margin: 0; padding: 0; box-sizing: border-box; }
  html, body {
    width: 1200px; height: 960px; overflow: hidden;
    background: var(--backdrop);
    font-family: "Roboto", Arial, sans-serif;
    color: var(--white);
  }
  .canvas { position: relative; width: 1200px; height: 960px; }

  .card {
    position: absolute; width: 600px; height: 343px;
    background: var(--navy); overflow: hidden;
  }
  .card--front { left: 302px; top: 124px; }
  .card--back  { left: 299px; top: 493px; }

  .splash { position: absolute; }
  .card--front .splash {
    left: 0; top: 0; width: 290px; height: 343px;
    background:
      radial-gradient(ellipse 60% 35% at 30% 95%, rgba(201,214,227,.55), transparent 70%),
      radial-gradient(ellipse 40% 50% at 50% 55%, rgba(95,120,150,.35), transparent 75%),
      radial-gradient(ellipse 70% 18% at 25% 2%, rgba(201,214,227,.45), transparent 80%),
      linear-gradient(90deg, rgba(95,120,150,.15), transparent);
  }
  .card--back .splash {
    right: 0; top: 0; width: 260px; height: 343px;
    background:
      radial-gradient(ellipse 55% 35% at 65% 92%, rgba(201,214,227,.55), transparent 70%),
      radial-gradient(ellipse 40% 50% at 55% 55%, rgba(95,120,150,.35), transparent 75%),
      radial-gradient(ellipse 70% 18% at 70% 2%, rgba(201,214,227,.45), transparent 80%),
      linear-gradient(270deg, rgba(95,120,150,.15), transparent);
  }

  .services {
    position: absolute; right: 42px; top: 60px;
    list-style: none; text-align: right;
    font-size: 15px; line-height: 24px;
  }
  .services li::after {
    content: ""; display: inline-block; width: 6px; height: 6px;
    border-radius: 50%; background: var(--coral);
    margin-left: 8px; vertical-align: middle;
  }

  .memberships { position: absolute; right: 44px; top: 262px; display: flex; gap: 26px; align-items: center; }
  .badge { background: var(--white); }
  .badge--shield { width: 30px; height: 34px; border-radius: 4px 4px 12px 12px; }
  .badge--wide { width: 92px; height: 22px; border-radius: 2px; }

  .brand {
    position: absolute; left: 112px; top: 40px;
    display: flex; align-items: center; gap: 12px;
  }
  .brand__mark { width: 18px; height: 18px; border-radius: 50%; background: var(--white); }
  .brand__name {
    font-size: 36px; font-weight: 500; line-height: 38px; color: var(--white);
  }

  .person {
    position: absolute; left: 30px; top: 172px;
    font-family: "Patrick Hand", cursive;
    font-size: 24px; color: var(--coral);
  }
  .contact { position: absolute; left: 30px; top: 208px; list-style: none; }
  .contact li { display: flex; align-items: center; gap: 7px; font-size: 16.5px; line-height: 21.5px; }
  .contact li.phones { font-weight: 700; font-size: 18px; line-height: 24px; }
  .contact svg { width: 14px; height: 14px; flex: none; fill: var(--coral); }
  .sep { margin: 0 10px; font-weight: 400; }
  .abn { position: absolute; left: 50px; top: 307px; font-size: 10px; }
</style>
</head>
<body>
<main class="canvas">

  <section class="card card--front" aria-label="Card front">
    <div class="splash" role="img" aria-label="Water splash photograph"></div>
    <ul class="services">
      <li>Complete Bathroom Renovations &amp; Remodelling</li>
      <li>Professional Service From Concept To Completion</li>
      <li>Highly Skilled &amp; Qualified Tradespeople</li>
      <li>All Work Guaranteed</li>
    </ul>
    <div class="memberships" aria-label="Industry memberships">
      <span class="badge badge--shield"></span>
      <span class="badge badge--wide"></span>
    </div>
  </section>

  <section class="card card--back" aria-label="Card back">
    <div class="splash" role="img" aria-label="Water splash photograph"></div>
    <div class="brand">
      <span class="brand__mark"></span>
      <span class="brand__name">Crestline<br>Bathrooms</span>
    </div>
    <p class="person">Daniel Morrow</p>
    <ul class="contact">
      <li class="phones">
        <svg viewBox="0 0 24 24"><path d="M6.6 10.8a15 15 0 0 0 6.6 6.6l2.2-2.2c.3-.3.7-.4 1-.2 1.1.4 2.3.6 3.6.6.6 0 1 .4 1 1V20c0 .6-.4 1-1 1A17 17 0 0 1 3 4c0-.6.4-1 1-1h3.5c.6 0 1 .4 1 1 0 1.3.2 2.5.6 3.6.1.3 0 .7-.2 1z"/></svg>
        0400 555 218<span class="sep">|</span>6200 4417
      </li>
      <li>
        <svg viewBox="0 0 24 24"><path d="M12 2a10 10 0 1 0 5 18.7l-1-1.7A8 8 0 1 1 20 12v1a2 2 0 0 1-4 0V7h-2v1a5 5 0 1 0 .6 7.3A4 4 0 0 0 22 13v-1A10 10 0 0 0 12 2zm0 13a3 3 0 1 1 0-6 3 3 0 0 1 0 6z"/></svg>
        daniel@crestlinebathrooms.com.au
      </li>
      <li>
        <svg viewBox="0 0 24 24"><path d="M12 2a10 10 0 1 0 0 20 10 10 0 0 0 0-20zm6.9 6h-3a15 15 0 0 0-1.3-3.6A8 8 0 0 1 18.9 8zM12 4a14 14 0 0 1 1.9 4h-3.8A14 14 0 0 1 12 4zM4.3 14a8 8 0 0 1 0-4h3.4a16 16 0 0 0 0 4zm.8 2h3a15 15 0 0 0 1.3 3.6A8 8 0 0 1 5.1 16zm3-8h-3a8 8 0 0 1 4.3-3.6A15 15 0 0 0 8.1 8zM12 20a14 14 0 0 1-1.9-4h3.8A14 14 0 0 1 12 20zm2.3-6H9.7a14 14 0 0 1 0-4h4.6a14 14 0 0 1 0 4zm.3 5.6a15 15 0 0 0 1.3-3.6h3a8 8 0 0 1-4.3 3.6zm1.7-5.6a16 16 0 0 0 0-4h3.4a8 8 0 0 1 0 4z"/></svg>
        crestlinebathrooms.com.au
      </li>
      <li>
        <svg viewBox="0 0 24 24"><path d="M2 5h20v14H2zm2 2v.5l8 5 8-5V7z"/></svg>
        PO Box 18 Karrabee 2600
      </li>
    </ul>
    <p class="abn">ABN 12 345 678 901</p>
  </section>

</main>
</body>
</html>
```